New Business Card Design Project

I need a design for business cards, i am an electrical business called "Corvane Electrical and Communications" i need the cards to be double sided with the company logo on the back (attached) the front needs to say my company name, web site, email address, telephone number, and ABN number and electrical license number. I am open to different arrangements of the information but would like the background to be incorporating something electrical or something that looks smart. open to all additional ideas also.

The company colours are orange and grey see logo attached.

Business Name: Corvane Electrical and Communications
Website: corvaneelectricalandcomms.example.com.au
Email: brent@corvaneelectricalandcomms.example.com.au
Telephone(mobile): 0481209736
ABN: 71208349162
Lic No: 418273D

Target Market(s)

Business entities, Project Managers, Accounts, Clients

Industry/Entity Type

Electrician

Contact Information for Business Card

I need a design for business cards, i am an electrical business called "Corvane Electrical and Communications" i need the cards to be double sided with the company logo on the back (attached) the front needs to say my company name

Font styles to use
Serif
Sans Serif

Colors
f37122
5c5c5c

Requirements
Must have
• Must have the Logo on the back open to different ways of it being on the back but had in mind to keep it central but again open to other options
Nice to have
• A real modern cool background that is eye catching yet contemporary
Should not have
• No backgrounds of a light bulb or plug or anything like that

```html
<!DOCTYPE html>
<html lang="en">
<head>
<meta charset="utf-8">
<title>Corvane Electrical and Communications – Business Cards</title>
<link rel="stylesheet" href="https://fonts.googleapis.com/css2?family=Open+Sans:wght@400;600&display=swap">
<style>
  :root {
    --canvas: #2b2b2b;
    --card: #050505;
    --orange: #f5a51c;
    --white: #ffffff;
    --grey: #5c5c5c;
  }
  * { margin: 0; padding: 0; box-sizing: border-box; }
  html, body {
    width: 1200px; height: 900px; overflow: hidden;
    background: var(--canvas);
    font-family: "Open Sans", Arial, sans-serif;
  }
  .sheet { position: relative; width: 1200px; height: 900px; }
  .card {
    position: absolute; left: 250px; width: 700px; height: 400px;
    background: var(--card); border-radius: 22px;
    box-shadow: 0 14px 30px rgba(0,0,0,.55);
    color: var(--white);
    overflow: hidden;
  }
  .card--logo { top: 40px; }
  .card--details { top: 460px; }

  .brand { position: absolute; display: flex; align-items: center; gap: 14px; }
  .brand__dot { width: 26px; height: 26px; border-radius: 50%; background: var(--orange); flex: none; }
  .brand__name { color: var(--white); font-weight: 600; line-height: 1.05; white-space: nowrap; }
  .brand__name .line-main { display: block; font-size: 64px; letter-spacing: 2px; }
  .brand__name .line-sub { display: block; font-size: 17px; letter-spacing: 1.5px; text-transform: uppercase; margin-top: 6px; }

  .card--logo .brand { left: 50%; top: 120px; transform: translateX(-50%); }
  .card--logo .web {
    position: absolute; bottom: 56px; left: 0; right: 0; text-align: center;
    font-size: 17px; color: var(--white);
  }
  .web .accent { color: var(--orange); }

  .card--details .brand { left: 40px; top: 128px; gap: 12px; }
  .card--details .brand__dot { width: 22px; height: 22px; }
  .card--details .brand__name .line-main { font-size: 46px; letter-spacing: 1.5px; }
  .card--details .brand__name .line-sub { font-size: 10.5px; letter-spacing: 1px; margin-top: 4px; }

  .contact { position: absolute; left: 352px; right: 30px; top: 146px; font-size: 12px; line-height: 1.55; }
  .contact__name { color: var(--orange); font-size: 24px; text-transform: uppercase; line-height: 1.1; white-space: nowrap; }
  .contact__role { font-size: 11px; text-transform: uppercase; margin-bottom: 10px; }
  .contact__row { display: flex; align-items: center; gap: 7px; white-space: nowrap; }
  .contact__row svg { width: 11px; height: 11px; flex: none; fill: none; stroke: var(--orange); stroke-width: 1.6; }
  .contact__label { color: var(--orange); }
</style>
</head>
<body>
<div class="sheet">

  <section class="card card--logo" aria-label="Card back">
    <div class="brand">
      <span class="brand__dot"></span>
      <div class="brand__name">
        <span class="line-main">Corvane</span>
        <span class="line-sub">Electrical &amp; Communications</span>
      </div>
    </div>
    <p class="web">www.<span class="accent">corvaneelectricalandcomms</span>.example.com.au</p>
  </section>

  <section class="card card--details" aria-label="Card front">
    <div class="brand">
      <span class="brand__dot"></span>
      <div class="brand__name">
        <span class="line-main">Corvane</span>
        <span class="line-sub">Electrical &amp; Communications</span>
      </div>
    </div>

    <div class="contact">
      <p class="contact__name">Marten Oakley</p>
      <p class="contact__role">Director</p>
      <p class="contact__row">
        <svg viewBox="0 0 12 12"><path d="M2 1.5h2.2l1 2.5-1.3 1a6 6 0 0 0 3.1 3.1l1-1.3 2.5 1V10A1.5 1.5 0 0 1 9 11.3 9 9 0 0 1 .7 3 1.5 1.5 0 0 1 2 1.5z"/></svg>
        0481-209-736
      </p>
      <p class="contact__row">
        <svg viewBox="0 0 12 12"><rect x="1" y="2.5" width="10" height="7" rx="1"/><path d="M1 3l5 3.5L11 3"/></svg>
        brent@corvaneelectricalandcomms.example.com.au
      </p>
      <p class="contact__row">
        <svg viewBox="0 0 12 12"><circle cx="6" cy="6" r="5"/><path d="M1 6h10M6 1c2.5 2.7 2.5 7.3 0 10M6 1c-2.5 2.7-2.5 7.3 0 10"/></svg>
        www.corvaneelectricalandcomms.example.com.au
      </p>
      <p class="contact__row"><span class="contact__label">ABN:</span> 71208349162</p>
      <p class="contact__row"><span class="contact__label">Lic No:</span> 418273D</p>
    </div>
  </section>

</div>
</body>
</html>
```